HAIR EXTENSIONS

We need a web design for a company base in Chicago called Tresses by Jolavie. We sale 100% human hair in Brazilian body wave deep wave straight or natural curl, Peruvian body wave straight or deep wave. Malaysian loose straight or body wave, in the chicago land.
We also ship hair to any city or country. We like to see design that use the colors pinks & grays, or would just like to see some design creative with colors thats inviting.

Also I'm using the quillmoss template, Home- banner contact us, about us, Features- product side/left sidebar, Shop- wish list /shopping cart/ tracking your order / checkout/ order received.
Porfolio-filterable 4column portfolio
Blog. Buy now

Industry/Entity Type

Hair

Number of Pages Required

4 page

Colors
aaaaaa
606060
dddddd
eea4c8
d3a5cc
b868aa
a6459a
ffc213
1b1b1b

Requirements
Must have
• I NEED THE DESIGNER TO DO THE 4 PAGE LIKE THIS.
• 1.HOME-PAGE BANNER CONTACT US SOME PRODUCT WITH SIDING IMAGES OF THE TOP PROUDCT
• 2.PRODUCT WITH SHOPPING CART- I WANT SIDING BARS FOR PRODUCT & SHOPPING CART WITH TRACKING YOUR ORDERS CHECK OUT & ORDER RECEIVED.
• 3.PORFOLIO PHOTO-I WANT A FEATURES FOR CUSTOMERS TO UPLOAN THERE PICTURE & BLOG ON THE PAGE
• 4.ABOUT US- TALK ABOUT ARE COMPAMY.
Nice to have
• hello designer
• I was working with a web developer for my site be for i came to craftnookly & they build a site for me that i liked, You all can view it at www.Tressesbyjolavie.info
• long story short never could get them to finish the project after they got paid!!
• I know, why paid before its finish bad decision. So know I'm here starting over with you all.
• here is a list of my competition site
• www.lockswellhub.com
• www.vanoraloft.com
• www.pellinoshop.com
• So just to give some insight, I'm looking for something like the one i had builded.

```html
<!DOCTYPE html>
<html lang="en">
<head>
<meta charset="utf-8">
<title>Jolavie — Hair Extensions</title>
<link href="https://fonts.googleapis.com/css2?family=Oswald:wght@300;400&family=Open+Sans:wght@400;600&display=swap" rel="stylesheet">
<style>
:root{
  --red:#e04848;
  --ink:#1b1b1b;
  --muted:#606060;
  --line:#aaaaaa;
  --soft:#dddddd;
  --white:#ffffff;
  --head:'Oswald',sans-serif;
  --body:'Open Sans',sans-serif;
}
*{margin:0;padding:0;box-sizing:border-box}
html,body{width:1200px;height:2507px;overflow:hidden;background:var(--white);color:var(--ink);font-family:var(--body)}
.page{position:relative;width:1200px;height:2507px}
.abs{position:absolute}
.head{font-family:var(--head);font-weight:300;text-transform:uppercase;white-space:nowrap}

/* header */
.topbar{left:0;top:0;width:1200px;height:90px;background:var(--red)}
.brand{left:52px;top:22px;display:flex;align-items:center;gap:14px;color:var(--white);font-family:var(--head);font-weight:400;font-size:30px;letter-spacing:.5px}
.brand-mark{width:40px;height:40px;border-radius:50%;background:var(--white)}
.account{right:80px;top:37px;color:var(--white);font-family:var(--head);font-weight:300;font-size:14px;letter-spacing:.5px}
.cart-icon{right:52px;top:34px}
.nav{left:0;top:90px;width:1200px;height:47px;border-bottom:1px solid var(--soft)}
.nav a{position:absolute;top:15px;transform:translateX(-50%);font-family:var(--head);font-weight:300;font-size:14px;color:var(--ink);text-decoration:none;text-transform:uppercase;white-space:nowrap}
.nav a.active{color:var(--red)}
.nav a.active::after{content:"";position:absolute;left:-3px;right:-3px;top:30px;height:3px;background:var(--red)}

/* hero */
.hero-band{left:0;top:359px;width:1200px;height:92px;background:var(--red)}
.hero-devices{left:75px;top:167px;width:545px;height:410px;border-radius:10px;background:linear-gradient(135deg,#c9b59a 0%,#2b3a6a 45%,#8a6458 75%,#d8d8d8 100%)}
.hero-kicker{left:718px;top:276px;color:var(--red);font-size:20px}
.hero-title{left:718px;top:302px;font-size:26px;color:var(--ink)}
.hero-bag{left:822px;top:370px}
.hero-caption{left:722px;top:466px;width:400px;font-size:11px;line-height:21px;text-transform:uppercase;color:var(--ink)}
.dots{left:579px;top:589px;display:flex;gap:7px}
.dots i{width:8px;height:8px;border-radius:50%;background:var(--ink)}
.dots i.on{background:var(--red)}

/* promos */
.promo{top:627px;width:521px;height:142px;border:3px solid var(--ink);padding:10px}
.promo-inner{width:100%;height:100%;border:1px solid var(--line);display:flex;flex-direction:column;align-items:center;justify-content:center;gap:6px}
.promo h2{font-family:var(--head);font-weight:400;font-size:27px;text-transform:uppercase;letter-spacing:-.3px}
.promo p{font-family:var(--head);font-weight:300;font-size:14px;text-transform:uppercase}

/* section titles */
.rule{left:52px;width:1096px;height:1px;background:var(--line)}
.rule::before{content:"";position:absolute;left:0;top:-2px;width:102px;height:5px;background:var(--red)}
.section-title{left:52px;font-size:22px}

/* product cards */
.card{top:902px;width:261px}
.card-photo{height:306px}
.card-actions{height:70px;background:var(--red);display:flex;color:var(--white);font-family:var(--head);font-weight:300;font-size:12px;text-transform:uppercase}
.card-actions span{flex:1;display:flex;align-items:center;justify-content:center;gap:8px}
.card-actions span+span{border-left:1px solid rgba(255,255,255,.35)}
.card-name{margin-top:24px;text-align:center;font-family:var(--head);font-weight:300;text-transform:uppercase;font-size:20px;line-height:30px;padding:0 20px}
.price{display:flex;align-items:center;justify-content:center;gap:8px;font-family:var(--head);font-weight:300;font-size:21px;margin-top:8px}

/* brands */
.brands{left:40px;top:1525px;width:1120px;height:75px;display:flex}
.brands li{list-style:none;flex:1;display:flex;align-items:center;justify-content:center;border-right:1px solid #eee;font-family:var(--body);font-weight:600;font-size:17px;color:var(--ink);text-transform:uppercase;letter-spacing:1px;text-align:center;line-height:1.05}
.brands li:last-child{border-right:0}

/* news */
.news-photo{top:1763px;width:180px;height:137px}
.news-title{top:1762px;color:var(--red);font-size:22px}
.news-date{top:1797px;font-size:10px;color:var(--muted);text-transform:uppercase}
.news-text{top:1838px;width:300px;font-size:10.5px;line-height:16px;color:var(--muted)}

/* footer columns */
.col-title{top:1963px;font-size:22px}
.col-rule{top:2008px;height:2px;background:var(--ink)}
.about-bag{left:52px;top:2040px;width:107px;height:112px;background:#eee}
.about-text{left:175px;top:2033px;width:130px;font-size:12px;line-height:20px;color:var(--ink)}
.contact-title{left:52px;top:2176px;font-size:17px}
.contact-lines{left:52px;top:2214px;font-size:12px;line-height:20px;text-transform:uppercase}
.mini{width:252px;height:90px;display:flex;gap:14px}
.mini-photo{width:87px;height:90px;flex:none}
.mini-name{font-family:var(--head);font-weight:300;font-size:15px;line-height:20px;text-transform:uppercase;margin-top:-3px}
.mini .price{justify-content:flex-start;font-size:21px;margin-top:4px}
.tags{left:896px;top:2037px;width:254px;height:126px}
.tags span{position:absolute;height:37px;border:1px solid var(--muted);display:flex;align-items:center;justify-content:center;font-family:var(--head);font-weight:300;font-size:13px;text-transform:uppercase;white-space:nowrap}
.tags span.on{background:var(--red);border-color:var(--red);color:var(--white)}
.social-title{left:896px;top:2180px;font-size:19px}
.social{left:896px;top:2244px;display:flex;gap:8px}
.social span{width:28px;height:28px;border:1px solid #c8c8c8;display:flex;align-items:center;justify-content:center;font-size:8px;color:var(--muted)}

/* footer */
.footer{left:0;top:2426px;width:1200px;height:81px;background:var(--red)}
.copyright{left:52px;top:2453px;font-size:10px;text-transform:uppercase;color:var(--white)}
.cards{right:20px;top:2444px;display:flex;gap:8px;align-items:center}
.cards span{width:36px;height:22px;background:var(--white);border-radius:2px;display:flex;align-items:center;justify-content:center;font-size:7px;font-weight:600;color:var(--ink)}
.cards b{font-size:10px;color:var(--white);font-weight:400;margin-left:4px}
</style>
</head>
<body>
<div class="page">

  <header>
    <div class="abs topbar"></div>
    <div class="abs brand"><span class="brand-mark"></span>JOLAVIE</div>
    <div class="abs account">REGISTER &nbsp;|&nbsp; SIGN IN</div>
    <svg class="abs cart-icon" width="22" height="20" viewBox="0 0 22 20" fill="none" stroke="#fff" stroke-width="2"><path d="M1 2h4l3 11h11l2-8H7"/><circle cx="9" cy="17" r="1.5" fill="#fff"/><circle cx="17" cy="17" r="1.5" fill="#fff"/></svg>
    <nav class="abs nav">
      <a class="active" style="left:219px">Home</a>
      <a style="left:327px">Categories</a>
      <a style="left:431px">Blog</a>
      <a style="left:550px">Your Experience</a>
      <a style="left:680px">About Us</a>
      <a style="left:820px">Online Beauty Store</a>
      <a style="left:964px">Subscribe</a>
    </nav>
  </header>

  <section class="hero">
    <div class="abs hero-band"></div>
    <div class="abs hero-devices" role="img" aria-label="Desktop, tablet and phone screens showing customers' curly hairstyles"></div>
    <div class="abs head hero-kicker">Choose your look</div>
    <h1 class="abs head hero-title">Buying and selling hair online today!</h1>
    <svg class="abs hero-bag" width="70" height="80" viewBox="0 0 70 80" fill="none" stroke="#fff" stroke-width="2.5"><path d="M8 28 L30 20 L62 34 L52 78 L14 70 Z"/><path d="M22 24 C20 6 40 4 40 26"/></svg>
    <p class="abs hero-caption">Velmora synthetic hair Crestline Edge custom lace wig<br>French wave</p>
    <div class="abs dots"><i></i><i class="on"></i><i></i></div>
  </section>

  <section>
    <div class="abs promo" style="left:52px"><div class="promo-inner"><h2>Get 25% off when you spend $100</h2><p>Limited time only-Jolavie</p></div></div>
    <div class="abs promo" style="left:626px"><div class="promo-inner"><h2>Free shipping on all orders</h2><p>Free over $125 for international orders</p></div></div>
  </section>

  <section>
    <div class="abs rule" style="top:827px"></div>
    <h2 class="abs head section-title" style="top:846px">Best Sellers</h2>

    <article class="abs card" style="left:52px">
      <div class="card-photo" role="img" aria-label="Young girl with beaded braids" style="background:linear-gradient(160deg,#e8e4ea,#2b3a6a 55%,#d9d3dc)"></div>
      <div class="card-actions"><span>&#128722;&nbsp;Add to cart</span><span>&#9673;&nbsp;Compare</span></div>
      <h3 class="card-name">Front wig Plumette(W/L Plumette)</h3>
      <div class="price"><svg width="14" height="14" viewBox="0 0 14 14"><path d="M1 7 7 1h6v6l-6 6z" fill="#1b1b1b"/><circle cx="10" cy="4" r="1.3" fill="#fff"/></svg>$19.99</div>
    </article>
    <article class="abs card" style="left:329px">
      <div class="card-photo" role="img" aria-label="Woman wearing a straight black wig" style="background:linear-gradient(160deg,#3a3030,#1b1b1b 45%,#7a5a50)"></div>
      <div class="card-actions"><span>&#128722;&nbsp;Add to cart</span><span>&#9673;&nbsp;Compare</span></div>
      <h3 class="card-name">Front wig Plumette(W/L Plumette)</h3>
      <div class="price"><svg width="14" height="14" viewBox="0 0 14 14"><path d="M1 7 7 1h6v6l-6 6z" fill="#1b1b1b"/><circle cx="10" cy="4" r="1.3" fill="#fff"/></svg>$19.99</div>
    </article>
    <article class="abs card" style="left:607px">
      <div class="card-photo" role="img" aria-label="Woman with braided updo" style="background:linear-gradient(170deg,#efe9e4,#6b4a35 45%,#4a3028)"></div>
      <div class="card-actions"><span>&#128722;&nbsp;Add to cart</span><span>&#9673;&nbsp;Compare</span></div>
      <h3 class="card-name">Front wig Plumette(W/L Plumette)</h3>
      <div class="price"><svg width="14" height="14" viewBox="0 0 14 14"><path d="M1 7 7 1h6v6l-6 6z" fill="#1b1b1b"/><circle cx="10" cy="4" r="1.3" fill="#fff"/></svg>$19.99</div>
    </article>
    <article class="abs card" style="left:886px">
      <div class="card-photo" role="img" aria-label="Two women smiling together" style="background:linear-gradient(150deg,#d8c8c0,#5a3a30 50%,#2a1c1a)"></div>
      <div class="card-actions"><span>&#128722;&nbsp;Add to cart</span><span>&#9673;&nbsp;Compare</span></div>
      <h3 class="card-name">Front wig Plumette(W/L Plumette)</h3>
      <div class="price"><svg width="14" height="14" viewBox="0 0 14 14"><path d="M1 7 7 1h6v6l-6 6z" fill="#1b1b1b"/><circle cx="10" cy="4" r="1.3" fill="#fff"/></svg>$19.99</div>
    </article>
  </section>

  <section>
    <div class="abs rule" style="top:1462px"></div>
    <h2 class="abs head section-title" style="top:1479px">Brands</h2>
    <ul class="abs brands">
      <li>Arvelli<br>Collezione</li>
      <li>Milo Reeve</li>
      <li>Borne</li>
      <li>Harrowby</li>
      <li>Jonah Spire</li>
      <li>Lena Vastrow</li>
      <li>Topmere</li>
    </ul>
  </section>

  <section>
    <div class="abs rule" style="top:1669px"></div>
    <h2 class="abs head section-title" style="top:1690px">Latest News</h2>

    <div class="abs news-photo" style="left:52px;background:linear-gradient(135deg,#6a3a50,#c04a7a 55%,#3a2028)" role="img" aria-label="Smiling woman with glossy curls"></div>
    <h3 class="abs head news-title" style="left:261px">Glorious Curls!</h3>
    <div class="abs news-date" style="left:263px">November 11, 2014</div>
    <p class="abs news-text" style="left:261px">Sed ut perspiciatis unde omnis iste natus error sit voluptatem accusantium doloremque laudantium, totam rem aperiam, eaque ipsa quae ab illo inventore veritatis et quasi architecto beatae vitae dicta sunt explicabo.</p>

    <div class="abs news-photo" style="left:643px;background:linear-gradient(170deg,#efe9e4,#6b4a35 45%,#4a3028)" role="img" aria-label="Woman with braided updo"></div>
    <h3 class="abs head news-title" style="left:852px">Glorious Curls!</h3>
    <div class="abs news-date" style="left:854px">November 11, 2014</div>
    <p class="abs news-text" style="left:852px">Sed ut perspiciatis unde omnis iste natus error sit voluptatem accusantium doloremque laudantium, totam rem aperiam, eaque ipsa quae ab illo inventore veritatis et quasi architecto beatae vitae dicta sunt explicabo.</p>
  </section>

  <section>
    <h2 class="abs head col-title" style="left:52px">About Us</h2>
    <div class="abs col-rule" style="left:52px;width:252px"></div>
    <div class="abs about-bag">
      <svg width="107" height="112" viewBox="0 0 107 112" fill="none" stroke="#1b1b1b" stroke-width="3"><path d="M30 38h50v54H30z"/><path d="M44 38c0-16 22-16 22 0"/></svg>
    </div>
    <p class="abs about-text">Lorem ipsum dolor sit amet, consectetur adipiscing elit. Quis que porta sapien nec leo convallis.</p>
    <h3 class="abs head contact-title">Contact Us:</h3>
    <div class="abs contact-lines">T: 1-866-555-0142<br>F: 1-866-555-0143<br>E: contact@jolavie.com</div>

    <h2 class="abs head col-title" style="left:336px">Top Rated</h2>
    <div class="abs col-rule" style="left:336px;width:251px"></div>
    <div class="abs mini" style="left:336px;top:2035px"><div class="mini-photo" role="img" aria-label="Woman with dark wavy hair" style="background:linear-gradient(135deg,#2b3a6a,#5a4048)"></div><div><div class="mini-name">Front wig Plumette(W/L Plumette)</div><div class="price"><svg width="14" height="14" viewBox="0 0 14 14"><path d="M1 7 7 1h6v6l-6 6z" fill="#1b1b1b"/><circle cx="10" cy="4" r="1.3" fill="#fff"/></svg>$19.99</div></div></div>
    <div class="abs mini" style="left:336px;top:2146px"><div class="mini-photo" role="img" aria-label="Blue curly hair close-up" style="background:linear-gradient(135deg,#2b3a8a,#1b2040)"></div><div><div class="mini-name">Front wig Plumette(W/L Plumette)</div><div class="price"><svg width="14" height="14" viewBox="0 0 14 14"><path d="M1 7 7 1h6v6l-6 6z" fill="#1b1b1b"/><circle cx="10" cy="4" r="1.3" fill="#fff"/></svg>$19.99</div></div></div>
    <div class="abs mini" style="left:336px;top:2266px"><div class="mini-photo" role="img" aria-label="Woman with short dark hair" style="background:linear-gradient(135deg,#4a2a28,#8a5a50)"></div><div><div class="mini-name">Front wig Plumette(W/L Plumette)</div><div class="price"><svg width="14" height="14" viewBox="0 0 14 14"><path d="M1 7 7 1h6v6l-6 6z" fill="#1b1b1b"/><circle cx="10" cy="4" r="1.3" fill="#fff"/></svg>$19.99</div></div></div>

    <h2 class="abs head col-title" style="left:617px">On Sale</h2>
    <div class="abs col-rule" style="left:617px;width:252px"></div>
    <div class="abs mini" style="left:617px;top:2035px"><div class="mini-photo" role="img" aria-label="Straight black wig" style="background:linear-gradient(135deg,#1b1b1b,#5a3a30)"></div><div><div class="mini-name">Front wig Plumette(W/L Plumette)</div><div class="price"><svg width="14" height="14" viewBox="0 0 14 14"><path d="M1 7 7 1h6v6l-6 6z" fill="#1b1b1b"/><circle cx="10" cy="4" r="1.3" fill="#fff"/></svg>$19.99</div></div></div>
    <div class="abs mini" style="left:617px;top:2146px"><div class="mini-photo" role="img" aria-label="Woman with braided hair" style="background:linear-gradient(135deg,#6b4a35,#3a2820)"></div><div><div class="mini-name">Front wig Plumette(W/L Plumette)</div><div class="price"><svg width="14" height="14" viewBox="0 0 14 14"><path d="M1 7 7 1h6v6l-6 6z" fill="#1b1b1b"/><circle cx="10" cy="4" r="1.3" fill="#fff"/></svg>$19.99</div></div></div>
    <div class="abs mini" style="left:617px;top:2266px"><div class="mini-photo" role="img" aria-label="Girl with beaded braids" style="background:linear-gradient(135deg,#dcdce8,#2b3a6a)"></div><div><div class="mini-name">Front wig Plumette(W/L Plumette)</div><div class="price"><svg width="14" height="14" viewBox="0 0 14 14"><path d="M1 7 7 1h6v6l-6 6z" fill="#1b1b1b"/><circle cx="10" cy="4" r="1.3" fill="#fff"/></svg>$19.99</div></div></div>

    <h2 class="abs head col-title" style="left:896px">Product Tags</h2>
    <div class="abs col-rule" style="left:896px;width:252px"></div>
    <div class="abs tags">
      <span class="on" style="left:0;top:0;width:87px">Black</span>
      <span style="left:93px;top:0;width:67px">Grey</span>
      <span style="left:166px;top:0;width:87px">Yellow</span>
      <span style="left:0;top:44px;width:160px">Glorious Curls!</span>
      <span style="left:166px;top:44px;width:87px">Natural</span>
      <span style="left:0;top:89px;width:87px">Virgin</span>
      <span style="left:93px;top:89px;width:52px">Shiny</span>
      <span style="left:150px;top:89px;width:103px">Uncut Virgin</span>
    </div>
    <h3 class="abs head social-title">Jolavie Social</h3>
    <div class="abs col-rule" style="left:896px;width:252px;top:2222px"></div>
    <div class="abs social"><span>Qo</span><span>Lu</span><span>Pi</span><span>Ra</span><span>Ve</span></div>
  </section>

  <footer>
    <div class="abs footer"></div>
    <div class="abs copyright">© 2014 Jolavie.com. All right reserved</div>
    <div class="abs cards"><span>VELA</span><span>MONTA</span><span>ORBIT</span><b>C3</b></div>
  </footer>

</div>
</body>
</html>
```